Snoutsaver.net Dog Coupon Site Website Design

TailThrift - Dog Coupon Site Design Brief

Project Overview
**Site Name:** SnoutSaver.net
**Purpose:** A modern coupon aggregation platform specifically for dog and pet-related products and services
**Target Audience:** Dog owners, pet enthusiasts, budget-conscious pet parents

Brand Identity & Visual Direction

Typography
- **Headers:** Modern sans-serif (Inter or similar) - Clean and friendly
- **Body:** Readable sans-serif with good mobile legibility
- **Accent:** Playful but professional font for coupon codes

Design Principles
- **Flat Design:** Clean, minimal with subtle shadows
- **Friendly & Approachable:** Rounded corners, soft edges
- **Trust-Building:** Clear pricing, transparent savings
- **Scannable:** Easy-to-read coupon codes and offers

## User Experience & Functionality

### Homepage Features
1. **Hero Section**
- Clear value proposition
- Search functionality
- Featured savings highlight

2. **Coupon Cards**
- One-click copy functionality
- Clear discount display
- Store/brand logos
- Expiration dates
- "Get Deal" call-to-action

3. **Navigation**
- Categories (Food, Toys, Health, Services, etc.)
- Popular stores
- Latest deals

### Interactive Elements
- **Copy Button:** Instant feedback when coupon copied
- **Deal Pages:** Detailed offer information, terms, store details
- **Search & Filter:** By category, store, discount amount
- **Mobile Menu:** Hamburger navigation for mobile

## Technical Requirements

### Responsive Design
- **Mobile-First:** Optimized for touch interactions
- **Tablet:** Adapted layout for medium screens
- **Desktop:** Full-width utilization with sidebar potential

### Performance
- **Fast Loading:** Optimized images, minimal JavaScript
- **Accessibility:** WCAG compliant, screen reader friendly
- **SEO Optimized:** Structured data for deals and offers

## Content Strategy

### Deal Categories
- Dog Food & Treats
- Toys & Accessories
- Health & Grooming
- Training & Services
- Outdoor & Travel

### Key Messaging
- "Save on everything your dog loves"
- "Verified deals updated daily"
- "Your pup deserves the best for less"

## Conversion Optimization

### Trust Elements
- Deal verification badges
- User reviews/ratings
- Clear savings calculations
- Expiration date transparency

### Call-to-Actions
- "Copy Code" (primary action)
- "Get Deal" (secondary action)
- "View All [Store] Deals"

## Success Metrics
- Coupon copy rate
- Click-through to retailer
- User return visits
- Mobile vs desktop usage
- Category performance

This design brief ensures a user-friendly, trustworthy platform that makes finding and using pet deals effortless while maintaining a warm, dog-loving community feel.

1. Design Objective
Create a warm, energetic space where dog lovers instantly feel welcomed and confident they’re finding genuine savings for their furry friends. Everything from the layout to the smallest icon should reinforce trust, delight, and simplicity.
2. Visual Personality
Color Palette: Soft, cheerful hues—think warm yellows and gentle blues—that evoke sunshine and playfulness without overwhelming.
Typography:
Headings: A modern, friendly sans‑serif (like Inter) with open letterforms to feel approachable.
Body Copy: Highly legible sans‑serif with generous line spacing for comfort on small screens.
Accent Font: A slightly quirky, hand‑drawn style used sparingly for coupon codes and special call‑outs, giving a personal, “paw‑picked” touch.
Imagery & Icons: Real‑life photographs of happy dogs interspersed with clean line‑icons of bones, paw prints, and hearts. Rounded shapes and subtle shadows keep the look soft and contemporary.
3. Layout & Hierarchy
Hero Area:
Full‑bleed image of a joyful dog, overlaid with a single, punchy tagline (“Save on everything your dog loves”).
Prominent search bar centered to invite exploration.
Offer Grid:
Generous white space around each coupon card so the eye can rest and scan easily.
Coupon cards feature a bold discount label, brand logo, and a friendly “Get Deal” button.
A playful “Copied!” animation briefly replaces the button once the code is grabbed.
Navigation:
A fixed header with clear category labels (Food, Toys, Health, Services).
A secondary “Popular Stores” carousel below to spotlight key partners.
4. Interaction & Motion
Micro‑interactions:
Hover state for cards subtly lifts the card and deepens its shadow, inviting a click.
Copy‑code button pulses once on hover, hinting at its one‑click magic.
Transitions:
Smooth fades between deal filters and search results to reassure users that the site is responding.
Loading indicators shaped like spinning collars or wagging tails to keep the theme consistent.
5. Accessibility & Inclusivity
Ensure all text meets contrast standards so every pet parent—regardless of vision—can read offers with ease.
Interactive elements sized for easy tapping on touchscreens.
Alt‑text for all imagery describing dogs, products, and actions for screen‑reader users.
6. Emotional Tone
From the moment someone lands on SnoutSaver.net, they should feel the joy of treating their dog without guilt. Friendly copy (“Your pup deserves the best for less”) paired with bright visuals will create a sense of community and shared passion.
7. Success by Design
Scan‑ability: Users should spot great deals in under two seconds.
Trust Signals: Badges (“Verified Savings”), clear expiration dates, and reviewer star icons should feel earned and prominent.
Return Visits: A “My Favorite Deals” heart icon encourages saving and returning, reinforced by subtle reminders in the UI.
This design approach keeps dog lovers front and center—making sure every graphic, font choice, and interaction feels like it was lovingly tailored for them.

Target Market(s)

Dog Lovers looking for good deals

Industry/Entity Type

Coupon Code

Number of Pages Required

4 page

Font styles to use
Sans Serif

Requirements
Must have
• Modern look, coupon copy cards it's a deal site and I want the coupon code and copy in the coupon card, blog section, review section, modern footer/header
Nice to have
• Modern coupon code website, easy to use

```html
<!DOCTYPE html>
<html lang="en">
<head>
<meta charset="utf-8">
<title>Snout Saver – Dog Deals &amp; Coupons</title>
<link rel="stylesheet" href="https://fonts.googleapis.com/css2?family=Lato:wght@400;700;900&display=swap">
<style>
:root{
  --green:#5c9a2a;
  --navy:#1e3a78;
  --ink:#1b1b1b;
  --text:#3a3a3a;
  --muted:#666;
  --line:#e4e4e4;
  --footer:#161616;
  --white:#fff;
}
*{box-sizing:border-box;margin:0;padding:0}
html,body{width:1200px;height:4545px;overflow:hidden}
body{font-family:"Lato",sans-serif;color:var(--text);background:var(--white);position:relative}
a{color:inherit;text-decoration:none}
.block{position:absolute;left:0;width:1200px}
.accent{color:var(--green)}
.section-title{font-size:42px;font-weight:700;color:var(--ink);line-height:1.1}
.section-sub{font-size:16px;color:var(--text);margin-top:18px}
.center{text-align:center}
.btn{display:inline-flex;align-items:center;justify-content:center;background:var(--navy);color:#fff;font-size:15px;font-weight:700;border-radius:3px}
.btn-green{background:var(--green)}

/* header */
.site-header{top:0;height:100px}
.logo{position:absolute;left:110px;top:26px;font-size:50px;font-weight:700;color:var(--ink);letter-spacing:-.5px}
.main-nav{position:absolute;left:440px;top:42px;display:flex;gap:0;font-size:15px}
.main-nav a{height:34px;display:flex;align-items:center;padding:0 10px;color:#333}
.main-nav a.active{background:var(--navy);color:#fff;border-radius:3px}
.main-nav a+a{margin-left:20px}

/* hero */
.hero{top:106px;left:34px;width:1132px;height:607px;border-radius:18px;overflow:hidden;
  background:linear-gradient(180deg,#fff 0%,#f3f2ed 22%,#c9c9b6 45%,#8f9a6c 62%,#7a6d55 80%,#6e6553 100%)}
.hero-inner{position:absolute;inset:0;text-align:center}
.hero h1{margin-top:32px;font-size:56px;font-weight:700;line-height:64px;color:var(--green)}
.hero h1 span{color:var(--navy);display:block}
.hero p{font-size:20px;color:#333;line-height:26px;margin:20px auto 0;width:440px}
.search{position:absolute;left:342px;top:256px;width:448px;height:42px;background:#fff;border-radius:21px;box-shadow:0 2px 8px rgba(0,0,0,.12);display:flex;align-items:center;padding:0 20px 0 30px;font-size:14px;color:#777;justify-content:space-between}
.dots{position:absolute;display:flex;gap:6px}
.dots i{width:11px;height:11px;border-radius:50%;background:#999;display:block}
.dots i:first-child{background:#fff;border:1px solid #999}
.hero .dots{left:530px;top:546px}
.hero .dots i{background:#666}

/* section heads with button */
.head-row{position:relative;height:100px}
.head-row .text{position:absolute;left:111px;top:0}
.head-row .btn{position:absolute;right:113px;top:18px;height:40px;padding:0 32px}

/* deal cards */
.deal-grid{position:absolute;left:102px;display:grid;grid-template-columns:repeat(3,322px);gap:17px 16px}
.deal-card{height:154px;background:#fff;border:1px solid var(--line);border-radius:8px;box-shadow:0 2px 10px rgba(0,0,0,.08);position:relative;padding:18px 0 0 17px}
.deal-card.hover{border:2px solid #8fc25f}
.deal-brand{font-size:18px;font-weight:700;color:var(--green)}
.deal-title{font-size:14px;line-height:19px;color:#333;width:148px;margin-top:6px}
.deal-expiry{font-size:9.5px;color:#555;margin-top:7px}
.deal-link{display:inline-block;margin-top:8px;font-size:15px;font-weight:700;color:var(--navy);text-decoration:underline}
.deal-photo{position:absolute;right:10px;top:8px;width:140px;height:137px;border-radius:6px}
.p1{background:linear-gradient(135deg,#c9a57a,#8b6a4a 60%,#6c7a8a)}
.p2{background:linear-gradient(135deg,#efe2d2,#6a4a32 55%,#e0b14a)}
.p3{background:linear-gradient(135deg,#3a3a3a,#e0b080 60%,#d9a13a)}
.p4{background:linear-gradient(135deg,#6f8fb8,#8a5a3a 55%,#e5e0d8)}
.p5{background:linear-gradient(135deg,#c9c4bc,#3a3a3a 50%,#d2c93a)}
.p6{background:linear-gradient(135deg,#d9c9b8,#a8623a 55%,#3d3a36)}

/* categories */
.cat-row{position:absolute;left:0;width:1200px;top:95px}
.cat{position:absolute;width:295px;text-align:center}
.cat-photo{width:295px;height:295px;border-radius:50%}
.c1{background:radial-gradient(circle,#7b4a2a,#a46a3e 60%,#c98f58)}
.c2{background:radial-gradient(circle at 50% 60%,#e8c3a0,#6a9a3a 55%,#2d5a2a)}
.c3{background:radial-gradient(circle,#d8b27a,#cfd6de 55%,#8a8f97)}
.cat-name{display:block;margin-top:18px;font-size:22px;font-weight:700;color:var(--navy)}

/* banner */
.banner{top:1913px;left:51px;width:1098px;height:334px;border-radius:16px;background:linear-gradient(120deg,#274684,#1f3f82 50%,#2a4a8a);text-align:center;color:#fff}
.banner h2{font-size:42px;font-weight:700;margin-top:74px}
.banner p{font-size:16px;line-height:26px;width:500px;margin:14px auto 0}
.banner .btn{margin-top:22px;height:41px;padding:0 22px;font-size:15px}

/* stores */
.stores{position:absolute;left:114px;top:106px;display:flex;gap:17px}
.store{width:124px;height:124px;border-radius:50%;background:#fff;box-shadow:0 2px 10px rgba(0,0,0,.15);display:flex;align-items:center;justify-content:center;font-size:17px;font-weight:700;color:var(--navy)}
.store.dark{background:#12152a;color:#fff}
.store.tan{background:#d9cbb8;color:#2a2a2a}

/* latest */
.latest-bg{top:2771px;height:579px;background:linear-gradient(180deg,#fff 0%,#fff 35%,#dfe6c8 55%,#8cab45 75%,#4e7d1e 100%)}

/* reviews */
.review{position:absolute;top:0;width:318px;height:227px;background:#fff;border:1px solid var(--line);border-radius:4px;padding:26px 24px}
.review.featured{background:var(--navy);color:#fff;border-color:var(--navy)}
.stars{color:#e86b1f;font-size:15px;letter-spacing:1px}
.review.featured .stars{color:#fff}
.review p{font-size:14px;line-height:22px;margin-top:18px}
.review h4{font-size:17px;font-weight:700;margin-top:20px}
.review time{display:block;font-size:13px;margin-top:8px}
.arrow{position:absolute;top:98px;width:32px;height:32px;border-radius:50%;background:var(--navy);display:flex;align-items:center;justify-content:center}

/* footer */
.site-footer{top:4123px;height:422px;background:var(--footer);color:#ddd}
.fcol{position:absolute;top:70px}
.fcol h3{font-size:20px;font-weight:700;color:#fff}
.fcol p,.fcol li{font-size:14px;line-height:26px}
.fcol ul{list-style:none;margin-top:20px}
.fcol li{margin-bottom:12px}
.contact-item{display:flex;gap:18px;margin-top:20px;align-items:flex-start}
.social{display:flex;gap:14px;margin-top:34px}
.social span{font-size:12px;font-weight:700;color:#fff;padding:6px 8px;border-radius:4px;background:#2a2a2a}
.social span:first-child{background:var(--green)}
.footer-bottom{position:absolute;left:0;top:383px;width:1200px;border-top:1px solid #333;text-align:center;font-size:12px;padding-top:12px;color:#ddd}
</style>
</head>
<body>

<header class="block site-header">
  <div class="logo">Snout Saver</div>
  <nav class="main-nav">
    <a class="active">Home</a><a>Coupon Cards</a><a>Categories</a><a>Popular Stores</a><a>Latest Deals</a><a>Contact</a>
  </nav>
</header>

<section class="block hero" role="img" aria-label="Young boy running down a country road walking a happy spaniel on a leash">
  <div class="hero-inner">
    <h1>Save On Everything Your <span>Dog Loves</span></h1>
    <p>Verified deals updated daily. Because your pup deserves the best for less.</p>
    <div class="search"><span>Search for food, toys, grooming...</span>
      <svg width="16" height="16" viewBox="0 0 16 16"><circle cx="7" cy="7" r="5" fill="none" stroke="#1e3a78" stroke-width="2"/><line x1="11" y1="11" x2="15" y2="15" stroke="#1e3a78" stroke-width="2"/></svg>
    </div>
    <div class="dots"><i></i><i></i><i></i><i></i></div>
  </div>
</section>

<section class="block" style="top:795px">
  <div class="head-row">
    <div class="text"><h2 class="section-title">Top Dog Deals <span class="accent">You Can't Miss</span></h2>
    <p class="section-sub">Sniff out fresh savings updated daily for all your pup's favorites.</p></div>
    <a class="btn">View All</a>
  </div>
  <div class="deal-grid" style="top:119px">
    <article class="deal-card"><h3 class="deal-brand">WoofCrate</h3><p class="deal-title">30% Off First Box of Toys + Treats</p><p class="deal-expiry">Expires in 2 days</p><a class="deal-link">Get Deal</a><div class="deal-photo p1" role="img" aria-label="Bowl of kibble with a toy ball"></div></article>
    <article class="deal-card"><h3 class="deal-brand">WoofCrate</h3><p class="deal-title">30% Off First Box of Toys + Treats</p><p class="deal-expiry">Expires in 2 days</p><a class="deal-link">Get Deal</a><div class="deal-photo p2" role="img" aria-label="Spaniel holding a yellow ball"></div></article>
    <article class="deal-card"><h3 class="deal-brand">WoofCrate</h3><p class="deal-title">30% Off First Box of Toys + Treats</p><p class="deal-expiry">Expires in 2 days</p><a class="deal-link">Copied!</a><div class="deal-photo p3" role="img" aria-label="Woman hugging her dog"></div></article>
    <article class="deal-card hover"><h3 class="deal-brand">WoofCrate</h3><p class="deal-title">30% Off First Box of Toys + Treats</p><p class="deal-expiry">Expires in 2 days</p><a class="deal-link">Get Deal</a><div class="deal-photo p4" role="img" aria-label="Owner with a border collie"></div></article>
    <article class="deal-card"><h3 class="deal-brand">WoofCrate</h3><p class="deal-title">30% Off First Box of Toys + Treats</p><p class="deal-expiry">Expires in 2 days</p><a class="deal-link">Copied!</a><div class="deal-photo p5" role="img" aria-label="Cat and dog eating from a bowl"></div></article>
    <article class="deal-card"><h3 class="deal-brand">WoofCrate</h3><p class="deal-title">30% Off First Box of Toys + Treats</p><p class="deal-expiry">Expires in 2 days</p><a class="deal-link">Get Deal</a><div class="deal-photo p6" role="img" aria-label="Owner cuddling a cavalier spaniel"></div></article>
  </div>
</section>

<section class="block center" style="top:1320px;height:520px">
  <h2 class="section-title">Browse Deals <span class="accent">By Category</span></h2>
  <p class="section-sub">Find savings tailored to every part of your pup's life.</p>
  <div class="cat-row">
    <div class="cat" style="left:114px"><div class="cat-photo c1" role="img" aria-label="Dog food and treats on a wooden table"></div><span class="cat-name">Dog Food &amp; Treats</span></div>
    <div class="cat" style="left:453px"><div class="cat-photo c2" role="img" aria-label="Terrier with a toy ball beside a crate of toys"></div><span class="cat-name">Toys &amp; Accessories</span></div>
    <div class="cat" style="left:790px"><div class="cat-photo c3" role="img" aria-label="Vet checking a dog with a stethoscope"></div><span class="cat-name">Health &amp; Grooming</span></div>
  </div>
  <div class="dots" style="left:565px;top:494px"><i style="background:var(--green);border:0"></i><i></i><i></i><i></i></div>
</section>

<section class="block banner" role="img" aria-label="Blue tinted photo of a pet owner with a dog">
  <h2>Your Pup Deserves The Best For Less</h2>
  <p>Why pay more? Give your furry friend top-quality care, treats, and toys—without breaking the bank.</p>
  <a class="btn btn-green">Start Saving Now</a>
</section>

<section class="block" style="top:2328px;height:270px">
  <div class="head-row">
    <div class="text"><h2 class="section-title">Shop Top <span class="accent">Pet Retailers</span></h2>
    <p class="section-sub">Fetch the best deals from your favorite trusted brands.</p></div>
    <a class="btn" style="top:41px;padding:0 28px">View All Store</a>
  </div>
  <div class="stores" style="top:129px">
    <div class="store">PupMart</div><div class="store dark">Tail Co</div><div class="store">FetchHub</div><div class="store tan">Bonely</div><div class="store">WagStore</div><div class="store dark">Kibblr</div><div class="store">PawCart</div>
  </div>
</section>

<div class="block latest-bg" role="img" aria-label="Fresh green grass field"></div>
<section class="block center" style="top:2663px">
  <h2 class="section-title">Latest <span class="accent">Verified Deals</span></h2>
  <p class="section-sub">Sniff out fresh savings updated daily for all your pup's favorites.</p>
  <div class="deal-grid" style="top:117px;text-align:left">
    <article class="deal-card"><h3 class="deal-brand">WoofCrate</h3><p class="deal-title">30% Off First Box of Toys + Treats</p><p class="deal-expiry">Expires in 2 days</p><a class="deal-link">Get Deal</a><div class="deal-photo p1" role="img" aria-label="Bowl of kibble with a toy ball"></div></article>
    <article class="deal-card"><h3 class="deal-brand">WoofCrate</h3><p class="deal-title">30% Off First Box of Toys + Treats</p><p class="deal-expiry">Expires in 2 days</p><a class="deal-link">Get Deal</a><div class="deal-photo p2" role="img" aria-label="Spaniel holding a yellow ball"></div></article>
    <article class="deal-card"><h3 class="deal-brand">WoofCrate</h3><p class="deal-title">30% Off First Box of Toys + Treats</p><p class="deal-expiry">Expires in 2 days</p><a class="deal-link">Copied!</a><div class="deal-photo p3" role="img" aria-label="Woman hugging her dog"></div></article>
    <article class="deal-card hover"><h3 class="deal-brand">WoofCrate</h3><p class="deal-title">30% Off First Box of Toys + Treats</p><p class="deal-expiry">Expires in 2 days</p><a class="deal-link">Get Deal</a><div class="deal-photo p4" role="img" aria-label="Owner with a border collie"></div></article>
    <article class="deal-card"><h3 class="deal-brand">WoofCrate</h3><p class="deal-title">30% Off First Box of Toys + Treats</p><p class="deal-expiry">Expires in 2 days</p><a class="deal-link">Copied!</a><div class="deal-photo p5" role="img" aria-label="Cat and dog eating from a bowl"></div></article>
    <article class="deal-card"><h3 class="deal-brand">WoofCrate</h3><p class="deal-title">30% Off First Box of Toys + Treats</p><p class="deal-expiry">Expires in 2 days</p><a class="deal-link">Get Deal</a><div class="deal-photo p6" role="img" aria-label="Owner cuddling a cavalier spaniel"></div></article>
  </div>
  <a class="btn" style="position:absolute;left:524px;top:468px;width:152px;height:42px">View All Deals</a>
</section>

<section class="block center" style="top:3428px">
  <h2 class="section-title">What Our <span class="accent">Customers Say</span></h2>
  <p class="section-sub">Sniff out fresh savings updated daily for all your pup's favorites.</p>
  <div style="position:absolute;left:0;top:127px;width:1200px;height:227px;text-align:left">
    <div class="arrow" style="left:55px"><svg width="12" height="12" viewBox="0 0 12 12"><path d="M8 1 3 6l5 5" fill="none" stroke="#fff" stroke-width="2"/></svg></div>
    <article class="review" style="left:111px"><div class="stars">★★★★★</div><p>Excepteur sint occaecat cupidatat non proident, sunt in culpa qui officia deserunt mollit anim id est laborum.</p><h4>Hallford</h4><time>May 30 2025</time></article>
    <article class="review featured" style="left:441px"><div class="stars">★★★★★</div><p>Excepteur sint occaecat cupidatat non proident, sunt in culpa qui officia deserunt mollit anim id est laborum.</p><h4>Renata</h4><time>May 30 2025</time></article>
    <article class="review" style="left:771px"><div class="stars">★★★★★</div><p>Excepteur sint occaecat cupidatat non proident, sunt in culpa qui officia deserunt mollit anim id est laborum.</p><h4>Odile</h4><time>May 30 2025</time></article>
    <div class="arrow" style="left:1113px"><svg width="12" height="12" viewBox="0 0 12 12"><path d="M4 1l5 5-5 5" fill="none" stroke="#fff" stroke-width="2"/></svg></div>
  </div>
</section>

<section class="block center" style="top:3862px">
  <h2 class="section-title">Verified Deals <span class="accent">Updated Daily</span></h2>
  <p class="section-sub" style="width:640px;margin:18px auto 0;line-height:26px">No expired codes, no fluff — just real savings for real dog lovers. From premium treats to durable toys — discover daily discounts from trusted pet brands.</p>
  <a class="btn" style="margin-top:24px;width:198px;height:42px">See Today's Coupons</a>
</section>

<footer class="block site-footer">
  <div class="fcol" style="left:113px;width:280px">
    <h3>About Us</h3>
    <p style="margin-top:18px">Whether you're a new pet parent or a seasoned dog lover, SnoutSaver is here to help you treat your pup for less — every single day.</p>
    <div class="social"><span>Yapper</span><span>Snapz</span><span>Linkio</span><span>Tubey</span></div>
  </div>
  <div class="fcol" style="left:462px;width:240px">
    <h3>Contact Us</h3>
    <div class="contact-item"><svg width="16" height="20" viewBox="0 0 16 20"><path d="M8 1a6 6 0 0 0-6 6c0 5 6 12 6 12s6-7 6-12a6 6 0 0 0-6-6z" fill="none" stroke="#ddd" stroke-width="1.5"/><circle cx="8" cy="7" r="2" fill="none" stroke="#ddd" stroke-width="1.5"/></svg><p>48 Snout Lane, Lorem ipsum dolor Na 67890.</p></div>
    <div class="contact-item"><svg width="16" height="16" viewBox="0 0 16 16"><path d="M3 1h3l1 4-2 1a9 9 0 0 0 5 5l1-2 4 1v3a2 2 0 0 1-2 2A13 13 0 0 1 1 3a2 2 0 0 1 2-2z" fill="none" stroke="#ddd" stroke-width="1.4"/></svg><p>+1 555 010 2040</p></div>
    <div class="contact-item"><svg width="16" height="14" viewBox="0 0 16 14"><rect x="1" y="2" width="14" height="10" fill="none" stroke="#ddd" stroke-width="1.4"/><path d="M1 2l7 6 7-6" fill="none" stroke="#ddd" stroke-width="1.4"/></svg><p>hello@snoutsaver.net</p></div>
  </div>
  <div class="fcol" style="left:752px">
    <h3>Quick Links</h3>
    <ul><li>Home</li><li>Coupon Cards</li><li>Categories</li><li>Popular Stores</li><li>Latest deals</li></ul>
  </div>
  <div class="fcol" style="left:976px">
    <h3>Other Links</h3>
    <ul><li>Contact</li><li>Review</li><li>Free Quote</li><li>Privacy Policy</li><li>Terms of Service</li></ul>
  </div>
  <div class="footer-bottom">Copyright © 2025 Snout Saver. All rights reserved.</div>
</footer>

</body>
</html>
```